Website Design Project for Beauty & Wellness Professionals

As background information, I have a website that is focused on Beauty & Wellness Professionals:
- Job Search (www.lumarinovo.com)
- Business Classifieds (negocios.lumarinovo.com)
- Freelancer Classifieds (freelancer.lumarinovo.com)
- Course Reviews (cursos.lumarinovo.com)

All those websites use standard templates.

I need a DESIGN for the HOME PAGE (no coding) of the Website Platform that consolidates the four platforms under the same design.

Website designs that we like:
- quelvox.com
- brintmoor.com

Target Market(s)

Brazilian Professionals from Beauty & Wellness sector

Industry/Entity Type

Business

Requirements
Must have
• Website designs that we like:
- quelvox.com
- brintmoor.com

```html
<!DOCTYPE html>
<html lang="pt-BR">
<head>
<meta charset="utf-8">
<title>Lumarinovo – Beleza &amp; Bem-Estar</title>
<link rel="stylesheet" href="https://fonts.googleapis.com/css2?family=Arimo:ital,wght@0,400;0,700;1,400;1,700&display=swap">
<style>
:root{
  --blue:#1769ad;
  --blue-dark:#0e4f8a;
  --link:#1f6fb8;
  --row-bg:#f2f6f9;
  --panel-bg:#eef3f7;
  --text:#222;
  --muted:#555;
  --orange:#e5875a;
  --page-active:#c9e4f2;
  --footer-a:#4f7fa6;
  --footer-b:#9cc3de;
  --chat:#b5895a;
}
*{box-sizing:border-box;margin:0;padding:0}
html,body{width:776px;height:1200px;overflow:hidden;background:#fff;font-family:"Arimo",Arial,sans-serif;color:var(--text)}
.page{position:relative;width:776px;height:1200px}

/* hero */
.hero{position:absolute;left:0;top:0;width:776px;height:290px;
  background:linear-gradient(180deg,#d8e8ef 0%,#b7d1de 35%,#e9e2dc 60%,#f4f4f2 78%,#3a73b0 100%)}
.topnav{position:absolute;top:0;left:0;width:776px;height:26px;background:rgba(255,255,255,.55);
  display:flex;align-items:center;justify-content:space-between;padding:0 68px 0 62px;font-size:8px;font-weight:700;color:var(--blue-dark)}
.platforms{display:flex;gap:14px}
.platforms span{color:var(--muted);font-weight:400}
.platforms .current{color:var(--blue-dark);font-weight:700}
.account{display:flex;gap:22px}
.brand{position:absolute;left:322px;top:41px;width:122px;height:83px;background:#fff;
  display:flex;flex-direction:column;align-items:center;justify-content:center;gap:8px}
.brand-dot{width:30px;height:30px;border-radius:50%;background:#5aa39a}
.brand-name{font-size:15px;color:#4b8fb0}
.search{position:absolute;left:95px;top:148px;width:579px;height:38px;background:var(--blue);
  display:flex;align-items:center;gap:6px;padding:0 6px}
.search .field{height:25px;background:#fff;font-size:9px;color:#999;display:flex;align-items:center;padding:0 8px}
.search .scope{width:86px;justify-content:space-between}
.search .keywords{width:202px}
.search .location{width:165px;margin-left:4px}
.search .btn{width:87px;height:25px;margin-left:4px;background:var(--orange);color:#fff;font-weight:700;font-size:10px;display:flex;align-items:center;padding-left:10px}
.search-note{position:absolute;top:194px;left:0;width:776px;text-align:center;font-size:9.5px;font-weight:700;color:#111}

/* main column */
.main-title{position:absolute;left:62px;top:309px;font-size:16px;font-weight:700;color:var(--blue-dark)}
.listing{position:absolute;left:62px;width:466px}
.tab{width:70px;height:22px;background:var(--blue);color:#fff;font-size:10px;font-weight:700;
  display:flex;align-items:center;justify-content:center;border-bottom:2px solid var(--blue-dark)}
.job{position:relative;height:66px;background:var(--row-bg);margin-bottom:3px}
.avatar{position:absolute;left:11px;top:8px;width:40px;height:40px;background:linear-gradient(135deg,#8a6a55,#d8b99c)}
.job-title{position:absolute;left:89px;top:8px;font-size:11.5px;font-weight:700;line-height:12.5px;width:190px}
.job-meta{position:absolute;left:90px;top:38px;font-size:7px;line-height:8px;color:var(--muted)}
.job-city{position:absolute;left:324px;top:22px;font-size:11px}
.job-date{position:absolute;left:411px;top:24px;font-size:7.5px;font-weight:700}
.pager{display:flex;justify-content:flex-end;gap:4px;margin:9px 4px 0 0}
.pager span{width:18px;height:18px;border:1px solid #ccd;background:#fff;font-size:7.5px;color:var(--link);display:flex;align-items:center;justify-content:center}
.pager .on{background:var(--page-active);font-weight:700;color:#333}
.pager .hover{background:#dceef7}

/* sidebar */
.side-head{position:absolute;left:535px;top:312px;width:162px;height:23px;background:var(--blue);color:#fff;font-size:13px;font-weight:700;padding:4px 0 0 8px}
.categories{position:absolute;left:535px;top:338px;width:162px;height:247px;background:var(--panel-bg);padding:10px 0 0 14px;list-style:none}
.categories li{font-size:8px;color:var(--link);height:16.8px;display:flex;align-items:center;gap:7px}
.categories li svg{width:8px;height:8px}
.categories .all{padding-left:10px}
.filters{position:absolute;left:538px;top:628px;width:154px}
.filter-tabs{display:flex;height:21px}
.filter-tabs span{font-size:7px;display:flex;align-items:center;padding:0 8px;background:#fff;border:1px solid #ddd;border-bottom:none}
.filter-tabs .alt{background:#ddd;color:#555}
.filter-item{height:20px;border:1px solid #ddd;border-top:none;font-size:7px;color:#444;display:flex;align-items:center;justify-content:space-between;padding:0 8px}
.filter-item:first-of-type{border-top:1px solid #ddd}
.testimonials{position:absolute;left:540px;top:750px;width:150px}
.testimonials h3{font-size:9.5px;color:var(--link);margin-bottom:13px}
.testimonials blockquote{font-size:8.5px;font-style:italic;font-weight:700;color:#aaa;line-height:11px;padding-left:10px;margin-bottom:10px}
.testimonials cite{display:block;font-size:8.5px;font-weight:700;color:#555;line-height:11px;padding-left:10px}

/* footer */
.footer{position:absolute;left:0;top:1046px;width:776px;height:154px;
  background:radial-gradient(circle at 40% 70%,var(--footer-b),var(--footer-a) 75%);color:#fff}
.footer-links{position:absolute;left:80px;top:20px;font-size:7.5px;line-height:18px}
.legal{position:absolute;left:83px;top:103px;font-size:7.5px;line-height:9px}
.social{position:absolute;left:628px;top:26px;display:flex;gap:3px}
.social span{width:20px;height:20px;border-radius:50%}
.social-count{position:absolute;left:681px;top:50px;font-size:7.5px}
.chat{position:absolute;left:555px;top:83px;width:138px;height:46px;background:var(--chat);border-radius:10px;padding:7px 0 0 11px}
.chat strong{font-size:11px;color:#333;display:block}
.chat small{display:block;font-size:6px;color:#555;text-align:right;padding-right:10px}
.offline{position:absolute;left:556px;top:136px;width:152px;height:18px;background:#2b2b2b;color:#fff;font-size:7px;display:flex;align-items:center;gap:4px;padding-left:8px}
.offline i{width:7px;height:7px;border-radius:50%;background:#aaa}
</style>
</head>
<body>
<div class="page">

  <header class="hero" role="img" aria-label="Foto de mulher relaxando em spa sobre toalhas, com orquídeas">
    <nav class="topnav">
      <div class="platforms">
        <span class="current">Vagas</span>
        <span>Negócios</span>
        <span>Freelancer</span>
        <span>Cursos</span>
      </div>
      <div class="account"><span>Anuncie VAGA EMPREGO</span><span>Entrar/Cadastre-se</span></div>
    </nav>
    <div class="brand"><span class="brand-dot"></span><span class="brand-name">Lumarinovo</span></div>
    <form class="search">
      <div class="field scope">Jobs
        <svg width="10" height="8" viewBox="0 0 10 8"><path d="M0 0h10L5 8z" fill="#666"/></svg></div>
      <div class="field keywords">Job Title, Keywords, Company</div>
      <div class="field location">Location</div>
      <div class="btn">SEARCH</div>
    </form>
    <p class="search-note">Search jobs from over 20,000 job sites, newspapers and company career pages</p>
  </header>

  <h1 class="main-title">Vagas de Emprego em Destaque</h1>

  <section class="listing" style="top:345px">
    <div class="tab">Featured</div>
    <div class="job"><div class="avatar" role="img" aria-label="Foto de perfil"></div>
      <div class="job-title">Aux. Cabeleireiro (Escovista) – Santo André (SP)</div>
      <div class="job-meta">Renata Vilela/Íris Cabelo e Estética –<br>Publicado por Renata Vilela</div>
      <div class="job-city">Santo André</div><div class="job-date">18 Jul 2013</div></div>
    <div class="job"><div class="avatar" role="img" aria-label="Foto de perfil"></div>
      <div class="job-title">Aux. Cabeleireiro (Escovista) – Santo André (SP)</div>
      <div class="job-city">Santo André</div><div class="job-date">18 Jul 2013</div></div>
    <div class="job"><div class="avatar" role="img" aria-label="Foto de perfil"></div>
      <div class="job-title">Aux. Cabeleireiro (Escovista) – Santo André (SP)</div>
      <div class="job-city">Santo André</div><div class="job-date">18 Jul 2013</div></div>
    <div class="job"><div class="avatar" role="img" aria-label="Foto de perfil"></div>
      <div class="job-title">Aux. Cabeleireiro (Escovista) – Santo André (SP)</div>
      <div class="job-meta">Renata Vilela/Íris Cabelo e Estética –<br>Publicado por Renata Vilela</div>
      <div class="job-city">Santo André</div><div class="job-date">18 Jul 2013</div></div>
    <div class="pager"><span>◂</span><span>1</span><span>2</span><span class="on">3</span><span>4</span><span class="hover">5</span><span>▸</span></div>
  </section>

  <section class="listing" style="top:682px">
    <div class="tab">Latest</div>
    <div class="job"><div class="avatar" role="img" aria-label="Foto de perfil"></div>
      <div class="job-meta">Renata Vilela/Íris Cabelo e Estética –<br>Publicado por Renata Vilela</div>
      <div class="job-city">Santo André</div><div class="job-date">18 Jul 2013</div></div>
    <div class="job"><div class="avatar" role="img" aria-label="Foto de perfil"></div>
      <div class="job-title">Aux. Cabeleireiro (Escovista) – Santo André (SP)</div>
      <div class="job-city">Santo André</div><div class="job-date">18 Jul 2013</div></div>
    <div class="job"><div class="avatar" role="img" aria-label="Foto de perfil"></div>
      <div class="job-title">Aux. Cabeleireiro (Escovista) – Santo André (SP)</div>
      <div class="job-city">Santo André</div><div class="job-date">18 Jul 2013</div></div>
    <div class="job"><div class="avatar" role="img" aria-label="Foto de perfil"></div>
      <div class="job-title">Aux. Cabeleireiro (Escovista) – Santo André (SP)</div>
      <div class="job-meta">Renata Vilela/Íris Cabelo e Estética –<br>Publicado por Renata Vilela</div>
      <div class="job-city">Santo André</div><div class="job-date">18 Jul 2013</div></div>
    <div class="pager"><span>◂</span><span>1</span><span>2</span><span class="on">3</span><span>4</span><span class="hover">5</span><span>▸</span></div>
  </section>

  <h2 class="side-head">Vagas de Emparego</h2>
  <ul class="categories">
    <li><svg viewBox="0 0 8 8"><path d="M0 4l3 3 5-6" stroke="#111" stroke-width="1.6" fill="none"/></svg>Auxiliar Cabeleireiro</li>
    <li><svg viewBox="0 0 8 8"><path d="M0 4l3 3 5-6" stroke="#111" stroke-width="1.6" fill="none"/></svg>Auxiliar Limpeza</li>
    <li><svg viewBox="0 0 8 8"><path d="M0 4l3 3 5-6" stroke="#111" stroke-width="1.6" fill="none"/></svg>Cabeleireiro</li>
    <li><svg viewBox="0 0 8 8"><path d="M0 4l3 3 5-6" stroke="#111" stroke-width="1.6" fill="none"/></svg>Depiladora</li>
    <li><svg viewBox="0 0 8 8"><path d="M0 4l3 3 5-6" stroke="#111" stroke-width="1.6" fill="none"/></svg>Designer Sobrancelha</li>
    <li><svg viewBox="0 0 8 8"><path d="M0 4l3 3 5-6" stroke="#111" stroke-width="1.6" fill="none"/></svg>Destaque</li>
    <li><svg viewBox="0 0 8 8"><path d="M0 4l3 3 5-6" stroke="#111" stroke-width="1.6" fill="none"/></svg>Enfermeira</li>
    <li><svg viewBox="0 0 8 8"><path d="M0 4l3 3 5-6" stroke="#111" stroke-width="1.6" fill="none"/></svg>Esteticista</li>
    <li><svg viewBox="0 0 8 8"><path d="M0 4l3 3 5-6" stroke="#111" stroke-width="1.6" fill="none"/></svg>Fisioterapeuta</li>
    <li><svg viewBox="0 0 8 8"><path d="M0 4l3 3 5-6" stroke="#111" stroke-width="1.6" fill="none"/></svg>Gerência/Coordenação</li>
    <li><svg viewBox="0 0 8 8"><path d="M0 4l3 3 5-6" stroke="#111" stroke-width="1.6" fill="none"/></svg>Manicure e Pedicure</li>
    <li><svg viewBox="0 0 8 8"><path d="M0 4l3 3 5-6" stroke="#111" stroke-width="1.6" fill="none"/></svg>Maquiador</li>
    <li class="all">View all categories</li>
  </ul>

  <aside class="filters">
    <div class="filter-tabs"><span>Buscar por</span><span class="alt">Tags</span></div>
    <div class="filter-item">Tipo de Vaga de Emprego<span>›</span></div>
    <div class="filter-item">Salário da Vaga<span>›</span></div>
    <div class="filter-item">Categoria da Vaga<span>›</span></div>
    <div class="filter-item">Data de Publicação<span>›</span></div>
  </aside>

  <aside class="testimonials">
    <h3>Testimonials</h3>
    <blockquote>Sed ut perspiciatis unde omnis iste natus error sit voluptatem accusantium doloremque laudantium</blockquote>
    <cite>Paulo Menezes, CEO<br>Casa Menezes</cite>
  </aside>

  <footer class="footer">
    <div class="footer-links">
      Vagas de Emprego - Beleza: Aux Cabeleireiro | Aux Escovista | Cabeleireiro | Depiladora | Manicure | Maquiador | Designer Sobrancelha<br>
      Vagas de Emprego - Saúde e Bem-Estar: Esteticista | Massoterapeuta | Podólogo | Fisioterapeuta | Enfermeira<br>
      Vagas de Emprego - Vendas e Admin: Recepção | Vendas Cosméticos | Auxiliar Limpeza | Gerência<br>
      Plataformas: www.lumarinovo.com | negocios.lumarinovo.com | freelancer.lumarinovo.com | cursos.lumarinovo.com
    </div>
    <div class="legal">COPYRIGHT 2013. ALL RIGHTS RESERVED.<br>TERMS &amp; CONDITIONS &nbsp;- &nbsp;PRIVACY &nbsp;- &nbsp;DISCLAIMER</div>
    <div class="social"><span style="background:#2f5ea3"></span><span style="background:#d3322c"></span><span style="background:#48a9e0"></span></div>
    <div class="social-count">X5</div>
    <div class="chat"><strong>Perguntas?</strong><small>Clique para falar conosco</small></div>
    <div class="offline"><i></i><b>Off-line</b> - Deixe sua Mensagem!</div>
  </footer>
</div>
</body>
</html>
```